Vitamin B12 Liquid Drops Label

hi, i need a label designed for my vitamin b12 drops that i am going to be selling on shopzello. the label needs to quickly capture the attention of a buyer as he or she is scrolling through the thumbnail search results on shopzello.com my brand is called nralo. i already have an example brand logo i will be using, however, i need help designing the rest of the label. attached are some examples of labels i like for other supplements.some of these examples are pink. i do not want pink. please go for a blue/green color scheme. THE DESIGN MUST BE BOLD

Target Market(s)

adults ages 30 - 64

Font styles to use
Sans Serif

Colors
0455a3
cedeed
3176b5
85acd3
cfdeed
9bcb3b
abd037
cadf82
00a990

Requirements
Must have
• - bold design
• - somewhat gender-neutral color scheme because this will be used equally by men and women
• - B12 MUST be very prominent and visible on the label
Should not have
• - it should not be "crunchy" looking

```html
<!DOCTYPE html>
<html lang="en">
<head>
<meta charset="utf-8">
<title>Nralo Vitamin B12 Drops Label</title>
<link rel="stylesheet" href="https://fonts.googleapis.com/css2?family=Montserrat:wght@500;700;800&display=swap">
<style>
  :root {
    --page-bg: #f2f2f2;
    --label-white: #ffffff;
    --aqua-light: #bfeef6;
    --aqua-mid: #6fd6ea;
    --aqua-deep: #3ec2e0;
    --violet: #5a3fb0;
    --violet-deep: #46309c;
    --text-light: #ffffff;
  }
  html, body {
    margin: 0;
    padding: 0;
    width: 1028px;
    height: 1200px;
    overflow: hidden;
    background: var(--page-bg);
    font-family: "Montserrat", sans-serif;
  }
  .label {
    position: absolute;
    left: 134px;
    top: 117px;
    width: 760px;
    height: 966px;
    display: block;
    box-shadow: 0 4px 18px rgba(0,0,0,0.08);
  }
  .brand-band { fill: var(--violet); }
  .brand-name { fill: var(--text-light); font-weight: 800; font-size: 56px; }
  .vitamin-word { fill: var(--violet); font-weight: 700; font-size: 46px; }
  .hero-b12 { fill: var(--violet-deep); font-weight: 800; font-size: 300px; }
  .drops-word { fill: var(--violet-deep); font-weight: 700; font-size: 44px; }
  .supplement-bar { fill: var(--violet-deep); }
  .supplement-text { fill: var(--text-light); font-weight: 700; font-size: 12px; letter-spacing: 0.2px; }
  .volume-text { fill: var(--violet-deep); font-weight: 700; font-size: 13px; }
</style>
</head>
<body>
<svg class="label" viewBox="0 0 388 493" xmlns="http://www.w3.org/2000/svg" aria-label="Nralo Vitamin B12 Drops label">
  <defs>
    <linearGradient id="aquaFade" x1="0" y1="0" x2="0.25" y2="1">
      <stop offset="0.35" stop-color="var(--label-white)"/>
      <stop offset="0.55" stop-color="var(--aqua-light)"/>
      <stop offset="0.8" stop-color="var(--aqua-mid)"/>
      <stop offset="1" stop-color="var(--aqua-deep)"/>
    </linearGradient>
  </defs>

  <rect class="label-ground" x="0" y="0" width="388" height="493" fill="url(#aquaFade)" role="img" aria-label="Aqua gradient background with bubble texture"/>

  <rect class="brand-band" x="0" y="0" width="73" height="266"/>
  <text class="brand-name" transform="translate(56 250) rotate(-90)" textLength="232" lengthAdjust="spacingAndGlyphs">NRALO</text>

  <text class="vitamin-word" transform="translate(70 490) rotate(-90)" textLength="172" lengthAdjust="spacingAndGlyphs">VITAMIN</text>

  <text class="hero-b12" transform="translate(310 470) rotate(-90)" textLength="470" lengthAdjust="spacingAndGlyphs">B12</text>

  <text class="drops-word" transform="translate(352 178) rotate(-90)" textLength="176" lengthAdjust="spacingAndGlyphs">DROPS</text>

  <rect class="supplement-bar" x="93" y="466" width="197" height="27"/>
  <text class="supplement-text" x="191.5" y="484" text-anchor="middle">DIETARY SUPPLEMENT</text>

  <text class="volume-text" x="356" y="453" text-anchor="middle">2 fl oz</text>
  <text class="volume-text" x="356" y="473" text-anchor="middle">(60ml)</text>
</svg>
</body>
</html>
```